Build a landing page to promote a service (dialler consultation and support).

We are a call centre consultation firm and we need a landing page to promote a service. The service is Tormalux dialler consultation and support.
If you do not know what Tormalux is, please do some quick "Zorvex" research for more information.
The landing page will be promoted with a paid advertisement, so we want something that is simple, and explains exactly what service we offer.
There are two objectives for the landing page:
1) A "call to action" which directs the user to a contact page, including a form plus all of our contact details.
2) A form for them viewers to enter their details to get a "FREE" quote for their project. This form should be placed on the main page.
Notes:
The call to action will require the viewer to enter their name, email, phone number as well as a description of their request. There will also need to be a drop down menu for the type of quote. This menu should have the following options:
1) Tormalux support
2) Tormalux hosting
3) Tormalux customisation
4) Other
We need 2 pages in total:
1) Main landing page
This is the home page. It will need to clearly indicate our services and our key selling features.
Services:
* Tormalux support
* Tormalux hosting
* Tormalux customisation
Key Selling Features:
* Australian based
* PCI complaint
* 10+ years of dialler and call centre experience
* we run a sister company which is a highly reputable 40 seat call centre, so we know first hand about call centre technology.
The main landing page will have an "about us" section with a few paragraphs about how we got started.
-------------------------------------------------------------------------
2) Contact page
All of our contact details will live on this page, as well as a contact form.
Other notes:
We will be self hosting the landing page.
We already have a domain name.
The design must be clean and incorporate our logo, as well as it's colours. (Logo attached)
We want a fully function HTML landing page, not just a "PSD" design.
The page must be mobile optimised.
Anyone using Tormalux software.

```html
<!DOCTYPE html>
<html lang="en">
<head>
<meta charset="utf-8">
<title>Contact Us – Ringwise</title>
<link href="https://fonts.googleapis.com/css2?family=Lato:wght@400;700&display=swap" rel="stylesheet">
<style>
:root{
  --brand-blue:#1b7fc3;
  --brand-teal:#2db39d;
  --ink:#222222;
  --muted:#3a3a3a;
  --hero-bg:#f3f3f3;
  --map-tone:#e4e6e2;
  --map-green:#cfe3c0;
  --field-border:#cfcfcf;
  --footer-bg:#262626;
  --footer-text:#e6e6e6;
  --white:#ffffff;
}
*{box-sizing:border-box;margin:0;padding:0}
html,body{width:1200px;height:1124px;overflow:hidden;background:var(--white);font-family:'Lato',sans-serif;color:var(--ink)}
.page{position:relative;width:1200px;height:1124px}

.site-header{position:absolute;left:0;top:0;width:1200px;height:133px;background:var(--white)}
.brand{position:absolute;left:74px;top:44px;display:flex;align-items:center;gap:10px}
.brand-dot{width:34px;height:34px;border-radius:50%;background:var(--brand-blue)}
.brand-name{font-size:32px;font-weight:700;color:var(--brand-blue);letter-spacing:0.5px}
.main-nav{position:absolute;top:54px;right:74px;display:flex;gap:38px;font-size:14.5px;text-transform:uppercase}
.main-nav a{color:var(--ink);text-decoration:none;display:flex;align-items:center;gap:6px}
.main-nav a.active{color:var(--brand-blue)}
.main-nav .caret{width:10px;height:10px;margin-left:8px}

.hero{position:absolute;left:0;top:133px;width:1200px;height:458px;background:var(--hero-bg);overflow:hidden}
.hero-map{position:absolute;inset:0;background:linear-gradient(135deg,var(--map-green) 0%,var(--map-tone) 35%,#dcdcd8 60%,var(--map-green) 100%);clip-path:polygon(600px 0,1200px 0,1200px 458px,508px 458px)}
.hero-text{position:absolute;left:74px;top:100px}
.hero-title{font-size:42px;font-weight:700;color:var(--brand-blue);margin-bottom:22px;margin-left:-1px}
.hero-address{font-size:15px;color:var(--ink);margin-bottom:16px}
.contact-list{list-style:none}
.contact-list li{display:flex;align-items:center;height:35px;font-size:15px}
.contact-list svg{width:14px;height:14px;margin-right:19px;fill:var(--ink)}

.quick-contact{position:absolute;left:0;top:633px;width:1200px;text-align:center}
.section-title{font-size:42px;font-weight:700;color:var(--brand-blue)}
.contact-form{position:absolute;left:210px;top:81px;width:782px;height:300px}
.field{position:absolute;border:1px solid var(--field-border);border-radius:2px;background:var(--white);font-size:14px;color:var(--muted);text-align:left;padding:0 11px;display:flex;align-items:center}
.field.half{width:378px;height:40px}
.field.col-right{left:404px}
.field.row-1{top:0}
.field.row-2{top:55px}
.field.select{justify-content:space-between;padding:0 16px}
.field.select svg{width:9px;height:12px;fill:var(--ink)}
.field.textarea{left:0;top:112px;width:782px;height:75px;align-items:flex-start;padding-top:11px}
.submit-btn{position:absolute;left:300px;top:210px;width:179px;height:52px;background:linear-gradient(180deg,var(--brand-teal),var(--brand-blue));color:var(--white);font-size:17px;font-weight:700;display:flex;align-items:center;justify-content:center;border:none}

.site-footer{position:absolute;left:0;top:1033px;width:1200px;height:91px;background:var(--footer-bg);color:var(--footer-text)}
.copyright{position:absolute;left:74px;top:38px;font-size:12px}
.social{position:absolute;right:74px;top:34px;display:flex;gap:14px;font-size:12px;font-weight:700}
.social span{display:flex;align-items:center;gap:5px}
.social i{width:8px;height:8px;border-radius:50%;background:var(--footer-text)}
</style>
</head>
<body>
<div class="page">
  <header class="site-header">
    <div class="brand"><span class="brand-dot"></span><span class="brand-name">Ringwise</span></div>
    <nav class="main-nav">
      <a href="#">Home</a>
      <a href="#">About Us</a>
      <a href="#">Services<svg class="caret" viewBox="0 0 10 10"><path d="M1.5 3.5 5 7l3.5-3.5" fill="none" stroke="#222" stroke-width="1.6"/></svg></a>
      <a href="#">Features</a>
      <a href="#" class="active">Contact Us</a>
    </nav>
  </header>

  <section class="hero">
    <div class="hero-map" role="img" aria-label="Street map showing the office location"></div>
    <div class="hero-text">
      <h1 class="hero-title">Contact Us</h1>
      <p class="hero-address">14 Harbour Lane, Brookfield City, USA</p>
      <ul class="contact-list">
        <li><svg viewBox="0 0 16 16"><path d="M3 1l3 3-1.5 2a9 9 0 0 0 5.5 5.5L12 10l3 3-2 2C7 15 1 9 1 3z"/></svg>1-800-555-0142</li>
        <li><svg viewBox="0 0 16 16"><path d="M3 1h8v4h3v10H2V5h1zM5 3v3h4V3zM5 8v2h2V8zm4 0v2h2V8zm-4 3v2h2v-2zm4 0v2h2v-2z"/></svg>1-800-555-0199</li>
        <li><svg viewBox="0 0 16 16"><path d="M1 3h14v2L8 9 1 5zm0 4 7 4 7-4v6H1z"/></svg>info@ringwise-mail.com</li>
        <li><svg viewBox="0 0 16 16"><path d="M8 1a5 5 0 0 1 5 5c0 4-5 9-5 9S3 10 3 6a5 5 0 0 1 5-5zm0 3a2 2 0 1 0 0 4 2 2 0 0 0 0-4z"/></svg>Map Direction</li>
      </ul>
    </div>
  </section>

  <section class="quick-contact">
    <h2 class="section-title">Quick Contact</h2>
    <form class="contact-form">
      <div class="field half row-1">Name</div>
      <div class="field half row-1 col-right">Email Address</div>
      <div class="field half row-2">Phone No</div>
      <div class="field half row-2 col-right select">Select Services<svg viewBox="0 0 9 12"><path d="M4.5 0 9 5H0zM0 7h9l-4.5 5z"/></svg></div>
      <div class="field textarea">Description</div>
      <div class="submit-btn">SUBMIT</div>
    </form>
  </section>

  <footer class="site-footer">
    <p class="copyright">Copyright ©2018 Company Name. All Rights Reserved.</p>
    <div class="social">
      <span><i></i>Linkra</span>
      <span><i></i>Chirpo</span>
      <span><i></i>Snapto</span>
      <span><i></i>Workly</span>
      <span><i></i>Vidora</span>
    </div>
  </footer>
</div>
</body>
</html>
```